NZ First of it's kind solutions directory and marketplace for busy Mums needs a business card design

We need a business card design for our new nationwide business in NZ (long term plans to go global). We provide solutions to the everyday challenges that busy Mums face by connecting them with quality communities and suppliers of carefully selected, relevant products and services. We sell direct via our online marketplace. The final design should communicate our values of inclusivity, quality and smart solutions. Colours should incorporate our logo colour palette of #477077 and #6ba8b2. Our website is at https://www.brightnestmums.example

Target Market(s)

busy Mums, Age 28 – 50, female, income over $100K, location main centres NZ primarily but NZ wide. Is likely juggling work or career with a young family. Probably had hobbies which have fallen by the wayside.
-Wants to succeed in her chosen career without compromising on family life
-to successfully juggle her career without feeling like she is compromising her children
- Is time poor, something always has to give and it’s generally her health (she’ll stay up late, get stressed)
- probably ex corporate or professional career. Has discretional income

Industry/Entity Type

Business

Contact Information for Business Card

Lena Forbisher, Founder, BrightNestMums.example (Strapline Tap; Gather; Sorted), 47 Kowhai Terrace, Ellerslie, Auckland 1051, New Zealand. Mob: 021 483 517 Ph: +64 (0)9 571 4860

Font styles to use
Other font styles liked:
• Raleway, and/or Architects Daughter

Colors
00a990
33b8a4
86cfc6
cfeae6

Requirements
Must have
• the above details, streamline. the logo and colours associated with those logos
Should not have
• foil or metallic colours

```html
<!DOCTYPE html>
<html lang="en">
<head>
<meta charset="utf-8">
<title>BrightNestMums — Business Card</title>
<link rel="stylesheet" href="https://fonts.googleapis.com/css2?family=Roboto:wght@400;500&family=Work+Sans:wght@400&display=swap">
<style>
  :root {
    --teal-dark: #477077;
    --teal-light: #6ba8b2;
    --paper: #ffffff;
    --backdrop: #dedede;
    --ink-white: #ffffff;
  }
  * { margin: 0; padding: 0; box-sizing: border-box; }
  html, body {
    width: 1200px; height: 897px; overflow: hidden;
    background: var(--backdrop);
  }
  .card {
    position: absolute;
    left: 303px;
    width: 595px;
    height: 338px;
    overflow: hidden;
  }
  .card--front { top: 92px; background: var(--paper); }
  .card--back { top: 469px; }

  /* Front */
  .brand {
    position: absolute;
    left: 32px; top: 52px;
    display: flex; align-items: center; gap: 12px;
  }
  .brand__dot {
    width: 30px; height: 30px; border-radius: 50%;
    background: var(--teal-dark);
  }
  .brand__name {
    font-family: "Roboto", sans-serif;
    font-weight: 500;
    font-size: 31px;
    letter-spacing: -0.5px;
    color: var(--teal-dark);
  }
  .holder {
    position: absolute;
    right: 31px; top: 160px;
    text-align: right;
    color: var(--teal-dark);
  }
  .holder__name {
    font-family: "Roboto", sans-serif;
    font-weight: 400;
    font-size: 29px;
    line-height: 34px;
  }
  .holder__role {
    font-family: "Work Sans", sans-serif;
    font-size: 14px;
    letter-spacing: 0.8px;
    line-height: 16px;
  }
  .divider {
    position: absolute;
    left: 32px; right: 31px; top: 223px;
    height: 1px; background: var(--teal-dark);
  }
  .contacts, .address {
    position: absolute;
    top: 250px;
    font-family: "Work Sans", sans-serif;
    font-size: 14.5px;
    letter-spacing: 0.9px;
    line-height: 19px;
    color: var(--teal-dark);
    list-style: none;
  }
  .contacts { left: 32px; }
  .contacts li { display: flex; align-items: center; gap: 6px; }
  .contacts svg { width: 9px; height: 10px; flex: none; }
  .address { right: 31px; text-align: right; }
  .bands { position: absolute; left: 0; bottom: 0; width: 595px; height: 30px; }

  /* Back */
  .photo {
    position: absolute; inset: 0;
    background:
      radial-gradient(ellipse 40% 55% at 45% 30%, #8a5a3a 0%, rgba(138,90,58,0) 70%),
      radial-gradient(ellipse 35% 45% at 70% 55%, #b58a55 0%, rgba(181,138,85,0) 70%),
      linear-gradient(180deg, #6d6660 0%, #85807b 55%, #6f6c6a 100%);
  }
  .back-brand {
    position: absolute;
    left: 0; right: 0; top: 152px;
    display: flex; justify-content: center; align-items: center; gap: 14px;
  }
  .back-brand .brand__dot { background: var(--ink-white); width: 36px; height: 36px; }
  .back-brand .brand__name { color: var(--ink-white); font-size: 40px; }
  .back-url {
    position: absolute;
    left: 0; right: 0; top: 296px;
    text-align: center;
    font-family: "Work Sans", sans-serif;
    font-size: 14.5px;
    letter-spacing: 1px;
    color: var(--ink-white);
  }
</style>
</head>
<body>

<section class="card card--front">
  <div class="brand">
    <span class="brand__dot"></span>
    <span class="brand__name">BrightNestMums</span>
  </div>

  <div class="holder">
    <p class="holder__name">Lena Forbisher</p>
    <p class="holder__role">Founder</p>
  </div>

  <div class="divider"></div>

  <ul class="contacts">
    <li>
      <svg viewBox="0 0 9 10" aria-hidden="true"><rect x="1.5" y="0.5" width="6" height="9" rx="1" fill="none" stroke="#477077"/></svg>
      021 483 517
    </li>
    <li>
      <svg viewBox="0 0 9 10" aria-hidden="true"><path d="M2 1 C0.5 4 3 8.5 7.5 9 L8 7.5 L6 6.5 L5 7.3 C3.8 6.6 2.8 5.2 2.6 3.8 L3.4 3 L2.8 1 Z" fill="#477077"/></svg>
      +64 (0)9 571 4860
    </li>
    <li>
      <svg viewBox="0 0 10 10" aria-hidden="true"><circle cx="5" cy="5" r="4.2" fill="none" stroke="#477077" stroke-width="0.8"/><ellipse cx="5" cy="5" rx="1.8" ry="4.2" fill="none" stroke="#477077" stroke-width="0.8"/><path d="M0.8 5 H9.2" stroke="#477077" stroke-width="0.8"/></svg>
      www.brightnestmums.example
    </li>
  </ul>

  <address class="address" style="font-style: normal;">
    47 Kowhai Terrace, Ellerslie<br>
    Auckland 1051, New Zealand
  </address>

  <svg class="bands" viewBox="0 0 595 30" aria-hidden="true">
    <polygon points="0,22 315,22 307,30 0,30" fill="var(--teal-light)"/>
    <polygon points="341,0 595,0 595,30 313,30" fill="var(--teal-dark)"/>
  </svg>
</section>

<section class="card card--back">
  <div class="photo" role="img" aria-label="Photograph of a tired mother resting her face in her hands, softly blurred in warm brown and grey tones"></div>
  <div class="back-brand">
    <span class="brand__dot"></span>
    <span class="brand__name">BrightNestMums</span>
  </div>
  <p class="back-url">www.brightnestmums.example</p>
</section>

</body>
</html>
```